Design a WordPress layout for a home loans company

The home loans company in question is going through a rebrand and needs a new website layout.
Sites they like: http://www.brightkeylending.com.au/
Current logo: Attached.
Colours to be used: As per those used in logo.
Primary: #71aa3d
Secondary: #130e10
Pages to be designed:
- Homepage
- Internal services page
Menu items for display purposes:
- Home
- About Us
- Speak to a Broker
- Articles
- Contact Us
A modern design with simplicity is key.
For copy, dummy text such as Lorem ipsum will be fine.
If you would like anything elso, please ask.
Target Market(s)
25-40 year old
Mostly female
Buying their first home in most cases
Industry/Entity Type
Mortgage Brokerage
Number of Pages Required
2 page

```html
<!DOCTYPE html>
<html lang="en">
<head>
<meta charset="utf-8">
<title>Nestwell Home Loans</title>
<link href="https://fonts.googleapis.com/css2?family=Quicksand:wght@500;700&family=Lato:wght@400;700&display=swap" rel="stylesheet">
<style>
:root{
  --green:#71aa3d;
  --green-dark:#5e9330;
  --ink:#130e10;
  --text:#333;
  --muted:#777;
  --line:#e2e2e2;
  --navy:#1d3b6a;
  --footer:#333333;
  --footer-bar:#272727;
  --white:#fff;
}
*{margin:0;padding:0;box-sizing:border-box}
html,body{width:1200px;height:3482px;overflow:hidden;background:var(--white)}
body{position:relative;font-family:"Lato",sans-serif;color:var(--text)}
.abs{position:absolute}
.heading{font-family:"Quicksand",sans-serif;color:var(--ink)}
.btn{position:absolute;display:flex;align-items:center;justify-content:center;border-radius:30px;font-family:"Lato",sans-serif;font-weight:700;font-size:17px;color:var(--white);white-space:nowrap}
.btn-green{background:var(--green);box-shadow:0 3px 0 var(--green-dark)}
.btn-dark{background:#2b2b2b;box-shadow:0 3px 0 #000}

/* header */
.topline{left:0;top:0;width:1200px;height:5px;background:var(--green)}
.brand{left:82px;top:38px;display:flex;align-items:center;gap:12px;font-family:"Quicksand",sans-serif;font-weight:700;font-size:24px;line-height:1.1;color:var(--green)}
.brand-mark{width:30px;height:30px;background:var(--green);flex:none}
.nav{left:0;top:0;height:128px}
.nav a{position:absolute;top:0;height:128px;display:flex;align-items:center;font-size:16px;color:#555;text-decoration:none;white-space:nowrap}
.nav a.active{background:var(--green);color:var(--white);justify-content:center;width:83px;left:323px}
.enquire{left:998px;top:42px;width:123px;height:51px;background:#000;box-shadow:none;font-size:18px}

/* hero */
.hero-photo{left:0;top:135px;width:1200px;height:643px;background:linear-gradient(90deg,#c9b7a6 0%,#e6ddd3 35%,#f4f4f4 60%,#f7f7f7 100%)}
.hero-title{left:724px;top:275px;font-size:42px;font-weight:700;line-height:1.05}
.hero-copy{left:724px;top:382px;width:420px;font-size:14px;line-height:1.6;color:#555}
.hero-wave{left:0;top:660px}

/* intro */
.intro-mark{left:570px;top:740px;width:60px;height:60px;border:6px solid var(--green)}
.center{left:0;width:1200px;text-align:center}
.intro-title{top:858px;font-size:36px;font-weight:500}
.intro-copy{left:260px;top:925px;width:680px;text-align:center;font-size:13.5px;line-height:1.85;color:#666}

/* services */
.services-bg{left:0;top:1154px;width:1200px;height:501px;background:linear-gradient(180deg,#d7d7d7,#ececec 55%,#f3f3f3)}
.services-title{top:1213px;font-size:36px;font-weight:500}
.card{top:1302px;width:334px;height:281px;background:var(--white);box-shadow:0 2px 6px rgba(0,0,0,.15)}
.card-icon{position:absolute;left:22px;top:24px;width:80px;height:80px;border-radius:50%;background:var(--green)}
.card-title{position:absolute;left:118px;top:30px;width:200px;font-family:"Quicksand",sans-serif;font-weight:700;font-size:22px;line-height:1.3;color:var(--green)}
.card-rule{position:absolute;left:0;top:130px;width:100%;height:1px;background:var(--line)}
.card-copy{position:absolute;left:22px;top:150px;width:295px;font-size:13.5px;line-height:1.9;color:#666}

/* broker finder */
.finder-title{left:80px;top:1776px;font-size:36px;font-weight:500}
.label{top:1864px;font-size:14px;font-weight:700;color:var(--ink)}
.field{top:1899px;width:292px;height:56px;border:1px solid var(--line);background:var(--white);font-size:13px;color:#777;padding:0 14px;display:flex;align-items:center}
.find-btn{left:77px;top:1980px;width:603px;height:56px;background:var(--green);color:var(--white);display:flex;align-items:center;justify-content:center;font-size:17px}
.finder-photo{left:726px;top:1720px;width:395px;height:383px;background:linear-gradient(135deg,#e9e6e1,#cfc6bb 60%,#9aa5b3)}

/* testimonial */
.testi-bg{left:0;top:2170px;width:1200px;height:464px;background:linear-gradient(90deg,#3e3e3e 0%,#4a4340 55%,#6b5450 100%)}
.quote{left:140px;top:2225px}
.testi-copy{left:142px;top:2293px;width:920px;font-size:14px;line-height:1.9;color:#eee}
.testi-name{left:142px;top:2397px;font-size:15px;color:var(--green);letter-spacing:.5px}
.testi-role{left:290px;top:2397px;font-size:15px;color:#eee}
.avatar{top:2458px;width:90px;height:90px;border-radius:50%;border:4px solid var(--white);background:#c8b8a8}
.avatar.active{border-color:var(--green);width:104px;height:104px;top:2452px}

/* blog */
.blog-title{top:2690px;font-size:38px;font-weight:500;color:var(--navy)}
.post-img{top:2781px;width:251px;height:209px;background:linear-gradient(135deg,#7c8794,#b6bcc4)}
.post-date{position:absolute;right:0;bottom:0;width:68px;height:72px;background:var(--green);color:var(--white);text-align:center;font-size:30px;line-height:1.2;padding-top:6px}
.post-date small{display:block;font-size:15px}
.post-title{top:2781px;width:240px;font-family:"Quicksand",sans-serif;font-weight:700;font-size:16.5px;line-height:1.5;color:var(--green)}
.post-title.dark{color:var(--ink)}
.post-meta{top:2846px;font-size:12.5px;color:#555;white-space:nowrap}
.post-copy{top:2885px;width:230px;font-size:13px;line-height:1.9;color:#999}
.dot{top:3040px;width:32px;height:5px;border:1px solid #bbb;border-radius:3px}
.dot.on{background:var(--green);border-color:var(--green)}

/* footer */
.footer{left:0;top:3115px;width:1200px;height:302px;background:var(--footer)}
.foot-link{left:80px;width:222px;font-size:14px;color:var(--white);border-bottom:1px solid #666;padding-bottom:10px}
.news-title{left:482px;top:3175px;font-family:"Quicksand",sans-serif;font-size:23px;color:var(--white);white-space:nowrap}
.news-field{left:434px;top:3243px;width:332px;height:58px;background:var(--white);border-radius:30px;overflow:hidden}
.news-field span{position:absolute;left:48px;top:20px;font-size:13px;color:#555}
.news-btn{position:absolute;right:0;top:0;width:96px;height:58px;background:var(--green);color:var(--white);font-size:15px;font-weight:700;display:flex;align-items:center;justify-content:center}
.social{top:3327px;width:44px;height:44px;border-radius:50%;background:var(--white)}
.contact{left:925px;font-size:13.5px;line-height:1.85;color:var(--white)}
.copyright{left:0;top:3417px;width:1200px;height:65px;background:var(--footer-bar);color:#ddd;font-size:13px;display:flex;align-items:center;justify-content:center}
.copyright b{margin:0 4px}
</style>
</head>
<body>

<!-- header -->
<div class="abs topline"></div>
<div class="abs brand"><span class="brand-mark"></span><span>Nestwell<br>Home Loans</span></div>
<nav class="abs nav">
  <a class="active">Home</a>
  <a style="left:440px">About Us</a>
  <a style="left:551px">Speak to a Broker</a>
  <a style="left:727px">Articles</a>
  <a style="left:825px">Contact Us</a>
  <svg style="position:absolute;left:942px;top:55px" width="22" height="22" viewBox="0 0 22 22" fill="none" stroke="#71aa3d" stroke-width="2"><circle cx="9" cy="9" r="7"/><line x1="14" y1="14" x2="20" y2="20"/></svg>
</nav>
<div class="btn enquire">ENQUIRE</div>

<!-- hero -->
<div class="abs hero-photo" role="img" aria-label="Family of four relaxing together at home reading a book"></div>
<h1 class="abs heading hero-title">Make Your Dreams<br>Come True</h1>
<p class="abs hero-copy">Your family deserves the most comfortable house to live.We help people to start a new life in a new place!</p>
<div class="btn btn-green" style="left:724px;top:464px;width:147px;height:56px">READ MORE</div>
<div class="btn btn-dark" style="left:890px;top:464px;width:157px;height:56px">CONTACT US</div>
<svg class="abs hero-wave" width="1200" height="130" viewBox="0 0 1200 130">
  <polygon points="0,75 600,20 1200,130 0,130" fill="#fff"/>
  <polygon points="0,58 600,24 600,40 0,78" fill="#71aa3d"/>
  <polygon points="600,24 1200,92 1200,118 600,40" fill="#71aa3d"/>
  <polygon points="0,78 600,40 1200,118 1200,130 0,130" fill="#fff"/>
</svg>

<!-- intro -->
<div class="abs intro-mark"></div>
<h2 class="abs heading center intro-title">Introducing Nestwell Home Loans</h2>
<p class="abs intro-copy">Lorem Ipsum is simply dummy text of the printing and typesetting industry. Lorem Ipsum has been the industry's standard dummy text ever since the 1500s, when an unknown printer took a galley of type and scrambled it to make a type specimen book.</p>
<div class="btn btn-green" style="left:523px;top:1033px;width:154px;height:53px">READ MORE</div>

<!-- services -->
<div class="abs services-bg" role="img" aria-label="Faded photo of a modern suburban house"></div>
<h2 class="abs heading center services-title">Nestwell Home Loans services</h2>
<div class="abs card" style="left:77px">
  <div class="card-icon"></div><div class="card-title" style="top:44px">Local experts</div><div class="card-rule"></div>
  <p class="card-copy">With brokers all across Australia, you can be confident there is a professional near you with in-depth knowledge of your local area.</p>
</div>
<div class="abs card" style="left:434px">
  <div class="card-icon"></div><div class="card-title">Ongoing trusted advice</div><div class="card-rule"></div>
  <p class="card-copy">We believe in the power of advice to help you both now and into the future as your circumstances and needs change.</p>
</div>
<div class="abs card" style="left:789px">
  <div class="card-icon"></div><div class="card-title" style="top:44px">Greater choice</div><div class="card-rule"></div>
  <p class="card-copy">Financial solutions aren't one-size-fits-all, and our extensive range of lenders and products ensures we have the right solution for each individual.</p>
</div>

<!-- broker finder -->
<h2 class="abs heading finder-title">Find a Local Broker</h2>
<div class="abs label" style="left:77px">Suburb/town</div>
<div class="abs label" style="left:392px">or postcode</div>
<div class="abs field" style="left:77px">Enter a location</div>
<div class="abs field" style="left:388px"></div>
<div class="abs find-btn">FIND BROKER</div>
<div class="abs finder-photo" role="img" aria-label="Broker showing a young couple around a bright new home"></div>

<!-- testimonial -->
<div class="abs testi-bg" role="img" aria-label="Smiling couple embracing, darkened background"></div>
<svg class="abs quote" width="62" height="50" viewBox="0 0 62 50" fill="#fff"><rect x="0" y="18" width="26" height="28" rx="3"/><path d="M0 22 Q2 4 22 0 L24 6 Q12 10 10 22Z"/><rect x="34" y="18" width="26" height="28" rx="3"/><path d="M34 22 Q36 4 56 0 L58 6 Q46 10 44 22Z"/></svg>
<p class="abs testi-copy">Lorem Ipsum is simply dummy text of the printing and typesetting industry. Lorem Ipsum has been the industry's standard dummy text ever since the 1500s, when an unknown printer took a galley of type and scrambled it to make a type specimen book. It has survived not only five centuries, but also the leap into electronic typesetting, remaining essentially unchanged.</p>
<div class="abs testi-name">MARA LINDEN</div>
<div class="abs testi-role">|&nbsp;&nbsp;&nbsp;&nbsp;&nbsp;Manager</div>
<div class="abs avatar active" style="left:142px" role="img" aria-label="Portrait of client"></div>
<div class="abs avatar" style="left:286px;background:#b9c3cf" role="img" aria-label="Portrait of client"></div>
<div class="abs avatar" style="left:410px;background:#cbbfb2" role="img" aria-label="Portrait of client"></div>

<!-- blog -->
<h2 class="abs heading center blog-title">Recent Blog</h2>
<div class="abs post-img" style="left:77px" role="img" aria-label="Team meeting around a laptop"><div class="post-date">20<small>July</small></div></div>
<div class="abs post-title" style="left:348px">Lorem Ipsum printing and typesetting industry.</div>
<div class="abs post-meta" style="left:348px">By Admin &nbsp;&nbsp;&nbsp;<span style="color:#71aa3d">♡</span> 200 &nbsp;&nbsp;&nbsp;&nbsp;&nbsp; 80</div>
<p class="abs post-copy" style="left:348px">Lorem Ipsum is simply dummy text of the printing and text is typesetting industry. Lorem Ipsum has been the industry's</p>
<div class="abs post-img" style="left:615px;background:linear-gradient(135deg,#d8d8d8,#8e8e8e)" role="img" aria-label="Two business people shaking hands by a window"><div class="post-date">20<small>July</small></div></div>
<div class="abs post-title dark" style="left:887px">Lorem Ipsum printing and typesetting industry.</div>
<div class="abs post-meta" style="left:887px">By Admin &nbsp;&nbsp;&nbsp;<span style="color:#71aa3d">♡</span> 200 &nbsp;&nbsp;&nbsp;&nbsp;&nbsp; 80</div>
<p class="abs post-copy" style="left:887px">Lorem Ipsum is simply dummy text of the printing and text is typesetting industry. Lorem Ipsum has been the industry's</p>
<div class="abs dot" style="left:541px"></div>
<div class="abs dot on" style="left:584px"></div>
<div class="abs dot" style="left:627px"></div>

<!-- footer -->
<footer class="abs footer"></footer>
<div class="abs foot-link" style="top:3175px">Home</div>
<div class="abs foot-link" style="top:3219px">About Us</div>
<div class="abs foot-link" style="top:3263px">Speak to a Broker</div>
<div class="abs foot-link" style="top:3303px">Articles</div>
<div class="abs foot-link" style="top:3345px;border:none">Contact Us</div>
<div class="abs news-title">Subscribe Newsletter</div>
<div class="abs news-field">
  <svg style="position:absolute;left:18px;top:22px" width="20" height="14" viewBox="0 0 20 14"><rect width="20" height="14" fill="#333"/><path d="M0 0 L10 8 L20 0" stroke="#fff" stroke-width="1.5" fill="none"/></svg>
  <span>Enter Your Email</span><div class="news-btn">SUBMIT</div>
</div>
<div class="abs social" style="left:497px"></div>
<div class="abs social" style="left:550px"></div>
<div class="abs social" style="left:602px"></div>
<div class="abs social" style="left:655px"></div>
<svg class="abs" style="left:890px;top:3174px" width="16" height="20" viewBox="0 0 16 20" fill="#71aa3d"><path d="M8 0a7 7 0 0 1 7 7c0 5-7 13-7 13S1 12 1 7a7 7 0 0 1 7-7z"/><circle cx="8" cy="7" r="2.5" fill="#333"/></svg>
<div class="abs contact" style="top:3170px;width:240px">Lorem Ipsum simply dummy printingtypesetting industry.</div>
<svg class="abs" style="left:889px;top:3238px" width="18" height="18" viewBox="0 0 24 24" fill="#71aa3d"><path d="M6.6 10.8a15 15 0 0 0 6.6 6.6l2.2-2.2a1 1 0 0 1 1-.25 11.4 11.4 0 0 0 3.6.6 1 1 0 0 1 1 1V20a1 1 0 0 1-1 1A17 17 0 0 1 3 4a1 1 0 0 1 1-1h3.5a1 1 0 0 1 1 1c0 1.25.2 2.45.6 3.6a1 1 0 0 1-.25 1z"/></svg>
<div class="abs contact" style="top:3235px">123-456-7890</div>
<svg class="abs" style="left:889px;top:3278px" width="18" height="13" viewBox="0 0 18 13"><rect width="18" height="13" fill="#71aa3d"/><path d="M0 0 L9 7 L18 0" stroke="#333" stroke-width="1.5" fill="none"/></svg>
<div class="abs contact" style="top:3272px">contact@nestwellhomeloans.com</div>
<div class="abs copyright">Copyright © <b>Nestwell Home Loans</b> - 2018 . All Right reserved</div>

</body>
</html>
```